Luxury Business Card Design for High-End Window Treatments

Gilded Slatworks
Custom Plantation Shutters & Architectural Shading Systems

⸻

BACK

Daniel Trevick
Owner

Custom Interior & Exterior Window Treatments

919-555-0148
gildedslatworks.com

I have included a picture that I’m hoping we can use on the back, but I’m also wondering if you can get rid of the ladder? Should we get rid of shutters , shades and blinds underneath Gilded Slatworks?

Target Market(s)

High-end residential homeowners, custom home builders, architects, interior designers, and luxury renovation clients seeking premium plantation shutters and motorized architectural shading systems.

Industry/Entity Type

Custom Window treatments

Contact Information for Business Card

Front Gilded Slatworks Custom Plantation Shutters Motorized Architectural Shading Systems BACK Daniel Trevick Owner 919-555-0148 GildedSlatworks.com Custom Interior & Exterior Window Treatments By Appointment

Requirements
Nice to have
• Not 100% sure on nice to halves or the color but you can definitely check out my website to get a better understanding of what I’m trying to do

```html
<!DOCTYPE html>
<html lang="en">
<head>
<meta charset="utf-8">
<title>Gilded Slatworks — Business Card</title>
<link rel="stylesheet" href="https://fonts.googleapis.com/css2?family=Libre+Baskerville&family=Poppins:wght@400&family=Roboto+Condensed:wght@700&display=swap">
<style>
  :root {
    --backdrop: #2a2a2b;
    --card: #1c1d1f;
    --gold: #c9a93f;
    --white: #ffffff;
    --sky-top: #8fc0ee;
    --facade: #3a4150;
    --porch: #9a9488;
  }
  * { box-sizing: border-box; margin: 0; padding: 0; }
  html, body { width: 1200px; height: 1108px; overflow: hidden; }
  body {
    background: var(--backdrop);
    display: flex;
    align-items: center;
    justify-content: center;
    gap: 70px;
  }
  .card {
    position: relative;
    width: 380px;
    height: 640px;
    border-radius: 22px;
    background: var(--card);
    overflow: hidden;
    box-shadow: 0 18px 40px rgba(0,0,0,.45);
  }
  .card-art { position: absolute; inset: 0; }
  .contact {
    position: absolute;
    left: 0; right: 0; top: 400px;
    text-align: center;
  }
  .contact-name {
    font-family: "Libre Baskerville", serif;
    color: var(--gold);
    font-size: 29px;
    line-height: 1.1;
  }
  .contact-role,
  .contact-line {
    font-family: "Poppins", sans-serif;
    color: var(--white);
    font-size: 17px;
    line-height: 1.35;
  }
  .rule {
    width: 56px; height: 2px;
    background: var(--gold);
    margin: 12px auto;
  }
  .tagline {
    font-family: "Libre Baskerville", serif;
    color: var(--gold);
    font-size: 15px;
    line-height: 1.5;
  }
  .brand-name {
    position: absolute;
    right: 46px; top: 330px;
    font-family: "Libre Baskerville", serif;
    color: var(--gold);
    font-size: 24px;
    line-height: 1.2;
    text-align: left;
  }
  .services {
    position: absolute;
    left: 0; right: 0; bottom: 60px;
    text-align: center;
    font-family: "Roboto Condensed", sans-serif;
    font-weight: 700;
    color: var(--white);
    font-size: 23px;
    line-height: 1.45;
  }
</style>
</head>
<body>

  <section class="card card-contact">
    <svg class="card-art" width="380" height="640" viewBox="0 0 380 640">
      <defs>
        <linearGradient id="porchTones" x1="0" y1="0" x2="0" y2="1">
          <stop offset="0" stop-color="var(--sky-top)"/>
          <stop offset="0.25" stop-color="#d9d3c4"/>
          <stop offset="0.45" stop-color="var(--facade)"/>
          <stop offset="1" stop-color="var(--porch)"/>
        </linearGradient>
      </defs>
      <polygon class="photo-area" role="img"
        aria-label="Photo of a home's covered porch with exterior motorized shades lowered"
        points="0,0 380,0 380,300 170,372 0,255"
        fill="url(#porchTones)"/>
      <polyline class="photo-edge" points="0,255 170,372 380,300"
        fill="none" stroke="var(--gold)" stroke-width="7"/>
    </svg>
    <div class="contact">
      <h1 class="contact-name">Daniel Trevick</h1>
      <p class="contact-role">Owner</p>
      <div class="rule"></div>
      <p class="contact-line">919-555-0148</p>
      <p class="contact-line">GildedSlatworks.com</p>
      <div class="rule"></div>
      <p class="tagline">Custom Interior &amp; Exterior<br>Window Treatments By Appointment</p>
    </div>
  </section>

  <section class="card card-brand">
    <p class="brand-name">Gilded<br>Slatworks</p>
    <p class="services">Gilded Slatworks Custom<br>Plantation Shutters Motorized<br>Architectural Shading Systems</p>
  </section>

</body>
</html>
```